SkyvornQ Business Cards and Stationary Design

Need a design for our business cards and stationary. I want to carry on the theme of the logo. I want the business cards to have a design on the back. I would like the business cards and the stationary to carry the same theme, design scheme, and branding

Target Market(s)

Airlines and Maintenance Facilities

Industry/Entity Type

Aviation

Contact Information for Business Card

Name
Position Title
Address: 4827 Trellis Hollow Road, Fort Pierce, Florida, 34951
Office Number
Mobile Number
Email
Website

Font styles to use
Serif
Sans Serif

Colors

Designer to choose colors to be used in the design.

```html
<!DOCTYPE html>
<html lang="en">
<head>
<meta charset="utf-8">
<title>SkyvornQ Business Card</title>
<link href="https://fonts.googleapis.com/css2?family=Montserrat:wght@700&family=PT+Sans:wght@400;700&family=PT+Sans+Narrow:wght@400;700&display=swap" rel="stylesheet">
<style>
  :root {
    --navy: #15284d;
    --navy-deep: #132a4f;
    --sky: #2a95d2;
    --royal: #233a7a;
    --white: #ffffff;
    --stage: #dcdddf;
    --stage-light: #e8e9eb;
  }
  * { margin: 0; padding: 0; box-sizing: border-box; }
  html, body { width: 1200px; height: 1103px; overflow: hidden; }
  body {
    background: linear-gradient(135deg, var(--stage-light), var(--stage));
    position: relative;
    font-family: "PT Sans", sans-serif;
  }
  .card {
    position: absolute;
    width: 788px;
    height: 451px;
    border-radius: 28px;
    overflow: hidden;
  }
  .card-front {
    left: 349px; top: 53px;
    background: var(--white);
    border: 1px solid #3a3a3a;
  }
  .card-back {
    left: 80px; top: 551px;
    background: var(--navy-deep);
  }
  .card-shapes { position: absolute; inset: 0; }
  .brand-mark {
    position: absolute;
    border-radius: 50%;
  }
  .card-front .brand-mark {
    left: 342px; top: 36px; width: 104px; height: 104px;
    border: 5px solid var(--navy);
  }
  .card-back .brand-mark {
    left: 321px; top: 116px; width: 146px; height: 146px;
    border: 7px solid var(--white);
  }
  .brand-name {
    position: absolute; left: 0; right: 0; text-align: center;
    font-family: "Montserrat", sans-serif; font-weight: 700;
    letter-spacing: 0.16em;
  }
  .card-front .brand-name {
    top: 152px; font-size: 38px; color: var(--navy);
    padding-left: 0.16em;
  }
  .card-back .brand-name {
    top: 286px; font-size: 50px; color: var(--white);
    padding-left: 0.16em; left: -8px;
  }
  .holder {
    position: absolute; left: 0; right: 0; top: 226px; text-align: center;
    font-family: "PT Sans Narrow", sans-serif; font-size: 27px; color: var(--navy);
  }
  .holder-name { font-weight: 700; }
  .holder-title { font-weight: 400; color: #1d2233; }
  .contact {
    position: absolute; left: 0; right: 0; text-align: center;
    color: var(--white); font-size: 18px; line-height: 1;
    display: flex; justify-content: center; gap: 12px; padding-left: 0;
  }
  .contact-item { display: inline-flex; align-items: center; gap: 5px; }
  .contact-item svg { width: 17px; height: 17px; }
  .contact-phones { top: 349px; left: -14px; }
  .contact-web { top: 382px; left: -22px; }
  .contact-address { top: 415px; left: -24px; }
  .back-url {
    position: absolute; left: 0; right: 0; top: 380px; text-align: center;
    color: var(--white); font-size: 25px; letter-spacing: 0.28em; left: -12px;
  }
</style>
</head>
<body>

<section class="card card-front">
  <svg class="card-shapes" viewBox="0 0 788 451" preserveAspectRatio="none" aria-hidden="true">
    <defs>
      <linearGradient id="swoosh" x1="0" x2="1" y1="0" y2="0">
        <stop offset="0" stop-color="#243571"/>
        <stop offset="0.35" stop-color="#244a8c"/>
        <stop offset="0.75" stop-color="#2a95d2"/>
        <stop offset="1" stop-color="#1f3f80"/>
      </linearGradient>
    </defs>
    <path d="M0 207 C 160 270, 380 320, 640 302 C 420 322, 170 300, 0 238 Z" fill="url(#swoosh)"/>
    <path d="M0 248 C 200 312, 560 345, 788 252 L 788 451 L 0 451 Z" fill="var(--navy)"/>
  </svg>
  <div class="brand-mark"></div>
  <div class="brand-name">SKYVORNQ</div>
  <p class="holder"><span class="holder-name">DORIAN KESSEL,</span> <span class="holder-title">PRESIDENT</span></p>

  <div class="contact contact-phones">
    <span class="contact-item">
      <svg viewBox="0 0 20 20" fill="none" stroke="#fff" stroke-width="1.6"><circle cx="10" cy="10" r="8.5"/><path d="M6.5 6c0 4 3.5 7.5 7.5 7.5l.8-1.8-2-1-1 1c-1.3-.6-2.4-1.7-3-3l1-1-1-2z" fill="#fff" stroke="none"/></svg>
      012-345-6789
    </span>
    <span class="contact-item">
      <svg viewBox="0 0 20 20" fill="none" stroke="#fff" stroke-width="1.6"><circle cx="10" cy="10" r="8.5"/><rect x="7" y="5" width="6" height="10" rx="1.2"/></svg>
      012-345-6789
    </span>
  </div>
  <div class="contact contact-web">
    <span class="contact-item">
      <svg viewBox="0 0 20 20" fill="none" stroke="#fff" stroke-width="1.6"><circle cx="10" cy="10" r="8.5"/><rect x="5.5" y="7" width="9" height="6.5" rx="1"/><path d="M5.5 7.5l4.5 3.5 4.5-3.5"/></svg>
      info@skyvornq.com
    </span>
    <span class="contact-item">
      <svg viewBox="0 0 20 20" fill="none" stroke="#fff" stroke-width="1.4"><circle cx="10" cy="10" r="8.5"/><ellipse cx="10" cy="10" rx="3.8" ry="8.5"/><path d="M1.5 10h17M3 5.5h14M3 14.5h14"/></svg>
      www.skyvornq.com
    </span>
  </div>
  <div class="contact contact-address">
    <span class="contact-item">
      <svg viewBox="0 0 20 20" fill="none" stroke="#fff" stroke-width="1.6"><circle cx="10" cy="10" r="8.5"/><path d="M10 15s-3.5-3.6-3.5-6a3.5 3.5 0 017 0c0 2.4-3.5 6-3.5 6z"/><circle cx="10" cy="9" r="1.2" fill="#fff"/></svg>
      123, Street Name, City Name, Zipcode-012345
    </span>
  </div>
</section>

<section class="card card-back">
  <div class="brand-mark"></div>
  <div class="brand-name">SKYVORNQ</div>
  <p class="back-url">www.skyvornq.com</p>
</section>

</body>
</html>
```